Bright Album Android app screenshots

I need some screenshot backgrounds that will be used as a background for Bright Album at https://apps.exampleshop.test/store/apps/details?id=com.lumenworks.album&hl=en-GB . I want to replace that boring orange background with something more exciting, maybe put some icons related to galleries there. Something like https://apps.exampleshop.test/store/apps/details?id=com.lumenworks.planner&hl=en-US has been done for the calendar. Let's keep it orange #F57C00 though and the resolution should be 2000x3555, I need 4 slightly different variants. Only the top and the sides of the background will be visible so focus on those parts. I need only the orange backgrounds, not the actual device or screenshot itself.

```html
<!DOCTYPE html>
<html lang="en">
<head>
<meta charset="utf-8">
<title>Bright Album – Screenshot Background</title>
<link href="https://fonts.googleapis.com/css2?family=Roboto:wght@400&display=swap" rel="stylesheet">
<style>
  :root {
    --orange-base: #FF9500;
    --orange-right: #FF8A00;
    --orange-deep: #FF7A00;
    --orange-stroke: #FF7500;
    --orange-soft: #FF8C00;
    --white: #FFFFFF;
  }
  html, body {
    margin: 0;
    padding: 0;
    width: 675px;
    height: 1200px;
    overflow: hidden;
    font-family: "Roboto", sans-serif;
  }
  .background {
    position: relative;
    width: 675px;
    height: 1200px;
    background: linear-gradient(90deg, var(--orange-base) 0%, var(--orange-right) 100%);
    overflow: hidden;
  }
  .background__art {
    position: absolute;
    inset: 0;
    width: 675px;
    height: 1200px;
  }
</style>
</head>
<body>
  <main class="background">
    <svg class="background__art" viewBox="0 0 675 1200" xmlns="http://www.w3.org/2000/svg" aria-hidden="true">
      <defs>
        <linearGradient id="deep-blob" x1="0" y1="0" x2="1" y2="0">
          <stop offset="0" stop-color="#FF8500"/>
          <stop offset="1" stop-color="#FF7700"/>
        </linearGradient>
        <filter id="soft-blur" x="-20%" y="-20%" width="140%" height="140%">
          <feGaussianBlur stdDeviation="2.2"/>
        </filter>
      </defs>

      <!-- darker sweep across the top left -->
      <path class="blob blob--top" fill="url(#deep-blob)"
            d="M0 0 H468 C420 90 370 180 340 247 C260 360 170 450 0 476 Z"/>

      <!-- pale arc at the very top -->
      <path class="blob blob--arc" fill="#FF9000" opacity="0.8"
            d="M145 0 C200 20 280 30 320 0 Z"/>

      <!-- lighter wave crossing the upper area -->
      <path class="blob blob--wave" fill="#FF9000" opacity="0.55"
            d="M0 89 C120 95 220 170 340 247 C460 320 560 330 675 300 L675 0 L630 0 C560 80 500 150 478 182 C520 225 560 250 600 265 L675 300 C560 330 460 320 400 290 C330 315 260 335 200 345 C130 345 60 330 0 318 Z"/>

      <!-- diagonal light band to the right -->
      <path class="blob blob--band" fill="#FF8E00" opacity="0.7"
            d="M634 0 H675 V300 C600 290 540 240 478 182 C540 120 590 55 634 0 Z"/>

      <!-- large outlined camera, top right -->
      <g class="icon icon--camera-large" transform="translate(512 42) rotate(20)"
         fill="none" stroke="var(--orange-stroke)" stroke-width="26" stroke-linejoin="round">
        <path d="M40 0 H170 V-20 Q170 -40 190 -40 H230 Q250 -40 250 -20 V0 H460 Q500 0 500 40 V275 Q500 315 460 315 H40 Q0 315 0 275 V40 Q0 0 40 0 Z"/>
        <circle cx="218" cy="148" r="102"/>
      </g>

      <!-- white folder icon -->
      <g class="icon icon--folder" transform="translate(30 226) rotate(-15 10 10)"
         fill="none" stroke="var(--white)" stroke-width="3" stroke-linejoin="round">
        <path d="M4 80 V8 Q4 3 9 3 H28 L36 9 H70 Q76 9 76 15 V20"/>
        <path d="M4 80 L18 26 Q20 20 26 20 H86 Q92 20 90 26 L78 74 Q76 80 70 80 Z"/>
      </g>

      <!-- small white camera at right edge -->
      <g class="icon icon--camera-small" transform="translate(633 555) rotate(20)"
         fill="none" stroke="var(--white)" stroke-width="5" stroke-linejoin="round">
        <path d="M8 0 H28 V-4 Q28 -9 33 -9 H40 Q45 -9 45 -4 V0 H80 Q88 0 88 8 V52 Q88 60 80 60 H8 Q0 60 0 52 V8 Q0 0 8 0 Z"/>
        <circle cx="46" cy="30" r="19"/>
      </g>

      <!-- blurred camera, bottom left -->
      <g class="icon icon--camera-blurred" transform="translate(-40 1058) rotate(-15)"
         filter="url(#soft-blur)" fill="none" stroke="#FFE3C2" stroke-width="5" stroke-linejoin="round" opacity="0.85">
        <path d="M10 0 H40 L48 -10 H100 Q110 -10 110 0 V70 Q110 80 100 80 H10 Q0 80 0 70 V10 Q0 0 10 0 Z"/>
        <circle cx="45" cy="42" r="22"/>
        <circle cx="92" cy="12" r="4" fill="#FFE3C2" stroke="none"/>
      </g>
    </svg>
  </main>
</body>
</html>
```